Garlic Farm for Farm Sales/Restaurant sales

Need a professional, but appealing to agriculture world. We are selling 27 kinds of Organic Garlic from a farm in Simla,CO. I have uploaded logo and business information-we are going to need a template, because I will need to use it for four separate people.
-We are trying to appeal to Farm to table restaurants
-As well as growers/farmers

Target Market(s)

Agriculture Sales/Restaurants-Organic

Industry/Entity Type

Agriculture

Contact Information for Business Card

Want it to look more unique then your average kelto stock card- I want it to look amazing

Font styles to use
Sans Serif

Colors
0455a3
ec1f27
fbed22
ffffff

Requirements
Must have
• Just be creative
Nice to have
• Colorful
Should not have
• plain

```html
<!DOCTYPE html>
<html lang="en">
<head>
<meta charset="utf-8">
<title>Ridgeline Garlic Co – Business Card</title>
<link rel="stylesheet" href="https://fonts.googleapis.com/css2?family=Open+Sans:wght@400;600;700&family=Satisfy&display=swap">
<style>
  :root {
    --backdrop: #d8d3ce;
    --card: #efedea;
    --navy: #17223b;
    --red: #b0121d;
    --gold: #f0b017;
    --ink: #4b505b;
  }
  * { margin: 0; padding: 0; box-sizing: border-box; }
  html, body {
    width: 1200px;
    height: 969px;
    overflow: hidden;
    background: var(--backdrop);
    font-family: "Open Sans", Arial, sans-serif;
  }
  .business-card {
    position: absolute;
    left: 75px;
    top: 185px;
    width: 1050px;
    height: 599px;
    border-radius: 24px;
    overflow: hidden;
    background: var(--card);
    box-shadow: 0 10px 30px rgba(0,0,0,0.18);
  }
  .card-art { position: absolute; inset: 0; }
  .brand {
    position: absolute;
    left: 54px;
    top: 205px;
    display: flex;
    align-items: center;
    gap: 14px;
  }
  .brand-dot {
    width: 44px;
    height: 44px;
    border-radius: 50%;
    background: var(--red);
  }
  .brand-name {
    font-weight: 700;
    font-size: 36px;
    line-height: 1;
    color: var(--navy);
    white-space: nowrap;
  }
  .address {
    position: absolute;
    left: 54px;
    top: 326px;
    font-size: 27px;
    line-height: 42px;
    color: var(--ink);
  }
  .contact-list {
    position: absolute;
    left: 54px;
    top: 432px;
    list-style: none;
    font-size: 27px;
    line-height: 41px;
    color: var(--ink);
  }
  .contact-list li { display: flex; align-items: center; gap: 12px; }
  .contact-icon { width: 24px; height: 24px; fill: var(--navy); }
  .person {
    position: absolute;
    right: 140px;
    top: 196px;
    text-align: right;
    white-space: nowrap;
  }
  .person-name {
    font-family: "Satisfy", cursive;
    font-size: 40px;
    color: var(--navy);
    line-height: 1.15;
  }
  .person-title {
    font-family: "Satisfy", cursive;
    font-size: 28px;
    color: var(--red);
    line-height: 1.2;
    margin-top: 6px;
  }
</style>
</head>
<body>
  <section class="business-card">
    <svg class="card-art" width="1050" height="599" viewBox="0 0 1050 599">
      <defs>
        <radialGradient id="markGlow" cx="50%" cy="45%" r="55%">
          <stop offset="0%" stop-color="#f3efe6"/>
          <stop offset="100%" stop-color="#dcd6cc"/>
        </radialGradient>
      </defs>
      <circle role="img" aria-label="Large faint brand mark decoration" cx="700" cy="230" r="265" fill="url(#markGlow)" opacity="0.7"/>
      <path class="navy-panel" d="M840 0 H1050 V599 H760 C900 520 960 380 950 230 C945 130 900 50 840 0 Z" fill="var(--navy)"/>
      <path class="swoosh-red" d="M560 599 C750 560 900 430 948 200 C944 420 850 560 720 599 Z" fill="var(--red)"/>
      <path class="swoosh-gold" d="M720 599 C850 560 932 450 955 320 C958 460 890 560 785 599 Z" fill="var(--gold)"/>
    </svg>

    <div class="brand">
      <span class="brand-dot"></span>
      <span class="brand-name">Ridgeline Garlic Co</span>
    </div>

    <p class="address">P.O. Box 218<br>Alder Flats, CO 80999</p>

    <ul class="contact-list">
      <li>
        <svg class="contact-icon" viewBox="0 0 24 24"><path d="M6.6 10.8a15.1 15.1 0 0 0 6.6 6.6l2.2-2.2a1 1 0 0 1 1-.25 11.4 11.4 0 0 0 3.6.57 1 1 0 0 1 1 1V20a1 1 0 0 1-1 1A17 17 0 0 1 3 4a1 1 0 0 1 1-1h3.5a1 1 0 0 1 1 1c0 1.25.2 2.45.57 3.6a1 1 0 0 1-.25 1z"/></svg>
        555-204-7316
      </li>
      <li>
        <svg class="contact-icon" viewBox="0 0 24 24"><path d="M2 5h20v14H2V5zm2 1.5 8 6.2 8-6.2H4z"/></svg>
        dana@ridgelinegarlic.com
      </li>
      <li>
        <svg class="contact-icon" viewBox="0 0 24 24"><path d="M12 2a10 10 0 1 0 0 20 10 10 0 0 0 0-20zm6.9 6h-3a15.7 15.7 0 0 0-1.3-3.9A8 8 0 0 1 18.9 8zM12 4c.8 1.2 1.5 2.5 1.9 4h-3.8c.4-1.5 1.1-2.8 1.9-4zM4.3 14a8.2 8.2 0 0 1 0-4h3.4a16.5 16.5 0 0 0 0 4H4.3zm.8 2h3a15.7 15.7 0 0 0 1.3 3.9A8 8 0 0 1 5.1 16zm3-8h-3a8 8 0 0 1 4.3-3.9A15.7 15.7 0 0 0 8.1 8zM12 20c-.8-1.2-1.5-2.5-1.9-4h3.8c-.4 1.5-1.1 2.8-1.9 4zm2.3-6H9.7a14.7 14.7 0 0 1 0-4h4.6a14.7 14.7 0 0 1 0 4zm.3 5.9a15.7 15.7 0 0 0 1.3-3.9h3a8 8 0 0 1-4.3 3.9zm1.7-5.9a16.5 16.5 0 0 0 0-4h3.4a8.2 8.2 0 0 1 0 4h-3.4z"/></svg>
        www.ridgelinegarlic.com
      </li>
    </ul>

    <div class="person">
      <p class="person-name">Dana Whitfield</p>
      <p class="person-title">CEO/Founder</p>
    </div>
  </section>
</body>
</html>
```